Modern looking signage for dental office.

Exterior signage for passing cars
Updates
Need extra days to review
Target Market(s)
Cars passing by
Font styles to use
Sans Serif
Colors
3276b5
Requirements
Must have
- Logo
- OPEN ON SUTURDAY AND SUNDAY
- NIGHT CLINIC AVAILABLE
- PLEASE USE THE FONT TYPE IN FILE 4 UPLOADED BELOW.
- (847) 302-7469
- Modern looking

```html
<!DOCTYPE html>
<html lang="en">
<head>
<meta charset="utf-8">
<title>Brightway Dental – Weekend &amp; Night Clinic Sign</title>
<link rel="stylesheet" href="https://fonts.googleapis.com/css2?family=Lato:wght@300;400;700;900&family=Roboto+Condensed:wght@300&display=swap">
<style>
  :root {
    --teal: #0b879c;
    --teal-deep: #0e7a90;
    --teal-light: #1b8ea3;
    --ink: #444547;
    --bar-grey: #5d5e60;
    --white: #ffffff;
    --haze-1: #f4f5f7;
    --haze-2: #e4efe9;
  }
  html, body {
    margin: 0;
    padding: 0;
    width: 1200px;
    height: 1200px;
    overflow: hidden;
    background: #ffffff;
  }
  .sign {
    position: relative;
    width: 1200px;
    height: 1200px;
    overflow: hidden;
    font-family: "Lato", sans-serif;
    background:
      radial-gradient(ellipse 260px 200px at 80px 520px, rgba(243,241,200,0.9), transparent 70%),
      radial-gradient(ellipse 300px 220px at 420px 470px, rgba(214,234,222,0.8), transparent 70%),
      radial-gradient(ellipse 260px 200px at 700px 520px, rgba(222,236,226,0.7), transparent 70%),
      radial-gradient(ellipse 400px 260px at 300px 760px, rgba(226,236,228,0.8), transparent 70%),
      linear-gradient(180deg, var(--haze-1) 0%, #f8f8fa 40%, var(--haze-2) 100%);
  }
  .sign h1, .sign p { margin: 0; }
  .tooth-visual {
    position: absolute;
    left: 824px;
    top: 401px;
    width: 376px;
    height: 720px;
    border-radius: 140px 40px 0 60px;
    background: linear-gradient(160deg, #ffffff 0%, #f2f3f4 45%, #dfe3e5 100%);
    opacity: 0.9;
  }
  .header-curves {
    position: absolute;
    left: 0;
    top: 0;
  }
  .brand-mark {
    position: absolute;
    left: 150px;
    top: 72px;
    width: 190px;
    height: 190px;
    border: 2px solid var(--ink);
    border-radius: 50%;
    box-sizing: border-box;
  }
  .brand-name {
    position: absolute;
    left: 366px;
    top: 120px;
    font-weight: 300;
    font-size: 70px;
    letter-spacing: 2px;
    color: var(--ink);
    line-height: 1;
    white-space: nowrap;
  }
  .tagline {
    position: absolute;
    left: 431px;
    top: 230px;
    font-family: "Roboto Condensed", sans-serif;
    font-weight: 300;
    font-size: 42px;
    line-height: 1;
    color: var(--ink);
    letter-spacing: 0.5px;
    white-space: nowrap;
  }
  .open-word {
    position: absolute;
    left: 78px;
    top: 472px;
    font-weight: 900;
    font-size: 194px;
    line-height: 1;
    color: var(--teal);
    letter-spacing: -2px;
  }
  .open-days {
    position: absolute;
    left: 621px;
    top: 494px;
    font-weight: 400;
    font-size: 76px;
    line-height: 81px;
    color: var(--ink);
    white-space: nowrap;
  }
  .night-bar {
    position: absolute;
    left: 112px;
    top: 703px;
    width: 976px;
    height: 75px;
    background: var(--bar-grey);
    display: flex;
    align-items: center;
    font-weight: 700;
    font-size: 49px;
    color: var(--white);
    white-space: nowrap;
  }
  .night-bar .lead { padding-left: 45px; padding-right: 8px; }
  .night-bar .hours {
    background: var(--teal);
    height: 75px;
    line-height: 75px;
    padding: 0 8px;
  }
  .night-bar .tail { padding-left: 8px; }
  .contact-band {
    position: absolute;
    left: 0;
    top: 835px;
    width: 1200px;
    height: 365px;
    background: linear-gradient(180deg, var(--teal-deep) 0%, var(--teal-deep) 42%, var(--teal-light) 42%, var(--teal) 100%);
    opacity: 0.96;
  }
  .phone-frame {
    position: absolute;
    left: 0;
    top: 835px;
  }
  .phone-number {
    position: absolute;
    left: 73px;
    top: 962px;
    width: 1053px;
    text-align: center;
    font-weight: 700;
    font-size: 150px;
    line-height: 158px;
    color: var(--white);
    letter-spacing: 1px;
  }
  .website {
    position: absolute;
    left: 0;
    top: 1142px;
    width: 1200px;
    text-align: center;
    font-weight: 400;
    font-size: 31px;
    color: var(--white);
  }
</style>
</head>
<body>
<main class="sign">
  <div class="tooth-visual" role="img" aria-label="Large white 3D molar tooth"></div>

  <svg class="header-curves" width="1200" height="460" viewBox="0 0 1200 460" aria-hidden="true">
    <path d="M0 136 Q 560 640 1200 220" fill="none" stroke="#444547" stroke-width="3"/>
    <path d="M0 198 Q 560 560 1200 185" fill="none" stroke="#0b879c" stroke-width="3"/>
  </svg>

  <div class="brand-mark"></div>
  <div class="brand-name">BRIGHTWAY DENTAL</div>
  <div class="tagline">MODERN GENERAL DENTISTRY</div>

  <h1 class="open-word">OPEN</h1>
  <p class="open-days">on SATURDAY<br>and SUNDAY</p>

  <div class="night-bar">
    <span class="lead">Night clinic from</span><span class="hours">5pm to 10pm</span><span class="tail">available</span>
  </div>

  <div class="contact-band"></div>

  <svg class="phone-frame" width="1200" height="300" viewBox="0 0 1200 300" aria-hidden="true">
    <path d="M462 126 H113 A40 40 0 0 0 73 166 V245 A40 40 0 0 0 113 285 H1086 A40 40 0 0 0 1126 245 V166 A40 40 0 0 0 1086 126 H598" fill="none" stroke="#ffffff" stroke-width="5"/>
    <circle cx="598" cy="66" r="59" fill="none" stroke="#ffffff" stroke-width="5"/>
    <path d="M573 48 l12 -6 l10 18 l-8 6 q6 14 18 22 l8 -6 l16 12 l-6 12 q-14 6 -32 -8 q-20 -16 -24 -34 q-2 -12 6 -16 z" fill="#ffffff"/>
    <path d="M602 44 a20 20 0 0 1 20 20" fill="none" stroke="#ffffff" stroke-width="4" stroke-linecap="round"/>
    <path d="M603 32 a32 32 0 0 1 32 32" fill="none" stroke="#ffffff" stroke-width="4" stroke-linecap="round"/>
  </svg>

  <div class="phone-number">847 302 7469</div>
  <div class="website">www.Brightwaydentalclinic.com</div>
</main>
</body>
</html>
```